Request for Business Card Design

Hi. My name is Marlene, I am looking for a new business card design for my company, Quarrow Signal Instruments, LLC. I really like the design you did for Tarsel Venture and was hoping you could do something similar using our full logo and our mark. I am also open to any raised texture design using our mark. I have attached our full logo, which would need to be somewhere on the card, as well as the mark in both outline and full form, as well as our brand colors / guide. The card does not have to be white, as long as our logo and mark appear. I actually like darker colored business cards more, but am open to all options. If you are interested in working with me, please let me know. We would also take the business card design into letterhead design if you can do that.

```html
<!DOCTYPE html>
<html lang="en">
<head>
<meta charset="utf-8">
<title>Quarrow Signal Instruments — Business Card</title>
<link href="https://fonts.googleapis.com/css2?family=Barlow:wght@400;500;700&display=swap" rel="stylesheet">
<style>
  :root {
    --stage: #8aa3c2;
    --stage-edge: #6e86aa;
    --card-dark: #3c3c3e;
    --card-dark-hi: #4a4a4c;
    --brand-orange: #f07430;
    --brand-orange-soft: #f6a26f;
    --role-tint: #ffe0cc;
    --white: #ffffff;
    --muted: #d9d9d9;
  }
  * { box-sizing: border-box; margin: 0; padding: 0; }
  html, body { width: 1200px; height: 876px; overflow: hidden; }
  body {
    background: radial-gradient(ellipse at 50% 35%, var(--stage) 0%, var(--stage-edge) 100%);
    font-family: "Barlow", Arial, sans-serif;
    position: relative;
  }
  .card {
    position: absolute;
    top: 286px;
    width: 530px;
    height: 303px;
    border-radius: 16px;
    overflow: hidden;
    box-shadow: 0 14px 30px rgba(30, 45, 70, 0.35);
  }
  /* Front */
  .card--front {
    left: 45px;
    background: linear-gradient(160deg, var(--card-dark-hi) 0%, var(--card-dark) 60%);
    color: var(--white);
  }
  .brand {
    position: absolute;
    top: 42px;
    left: 190px;
    display: flex;
    align-items: center;
    gap: 12px;
  }
  .brand__dot {
    width: 34px; height: 34px;
    border-radius: 50%;
    background: var(--white);
  }
  .brand__name { font-weight: 700; color: var(--white); line-height: 1; }
  .brand__name .line1 { display: block; font-size: 34px; letter-spacing: 4px; }
  .brand__name .line2 { display: block; font-size: 9.5px; letter-spacing: 1px; margin-top: 4px; }
  .band-rule { position: absolute; left: 0; width: 100%; height: 3px; background: var(--white); }
  .band-rule--top { top: 122px; }
  .band-rule--bottom { top: 186px; }
  .band {
    position: absolute; left: 0; top: 131px; width: 100%; height: 49px;
    background: var(--brand-orange);
  }
  .person {
    position: absolute; top: 131px; left: 40px; height: 49px;
    display: flex; flex-direction: column; justify-content: center;
    line-height: 1.1;
  }
  .person__name { font-size: 20px; font-weight: 500; letter-spacing: 0.5px; color: var(--white); text-transform: uppercase; }
  .person__role { font-size: 12px; color: var(--role-tint); margin-left: 22px; }
  .contacts {
    position: absolute; left: 22px; right: 18px; top: 222px;
    display: flex; justify-content: space-between;
  }
  .contact { display: flex; align-items: flex-start; gap: 8px; font-size: 12.5px; color: var(--muted); line-height: 1.35; white-space: nowrap; }
  .contact__icon {
    flex: 0 0 auto; width: 22px; height: 22px; border-radius: 50%;
    background: var(--white); display: flex; align-items: center; justify-content: center;
  }
  /* Back */
  .card--back {
    left: 625px;
    background: linear-gradient(150deg, var(--brand-orange-soft) 0%, var(--brand-orange) 45%);
    display: flex; align-items: center; justify-content: center;
  }
  .back-name { color: var(--white); font-weight: 700; text-align: center; line-height: 1.05; }
  .back-name .line1 { display: block; font-size: 52px; letter-spacing: 6px; }
  .back-name .line2 { display: block; font-size: 16px; letter-spacing: 2px; margin-top: 8px; }
</style>
</head>
<body>
  <section class="card card--front" aria-label="Business card front">
    <div class="brand">
      <span class="brand__dot"></span>
      <span class="brand__name"><span class="line1">QUARROW</span><span class="line2">SIGNAL INSTRUMENTS</span></span>
    </div>
    <div class="band-rule band-rule--top"></div>
    <div class="band"></div>
    <div class="band-rule band-rule--bottom"></div>
    <div class="person">
      <div class="person__name">Marlene Torvik</div>
      <div class="person__role">Director</div>
    </div>
    <div class="contacts">
      <div class="contact">
        <span class="contact__icon">
          <svg width="10" height="14" viewBox="0 0 10 14"><rect x="1" y="0.5" width="8" height="13" rx="1.5" fill="none" stroke="#3c3c3e" stroke-width="1.4"/><circle cx="5" cy="11" r="0.9" fill="#3c3c3e"/></svg>
        </span>
        <span>+65 6123 4580<br>+65 8123 7744</span>
      </div>
      <div class="contact">
        <span class="contact__icon">
          <svg width="14" height="10" viewBox="0 0 14 10"><rect x="0.7" y="0.7" width="12.6" height="8.6" rx="1" fill="none" stroke="#3c3c3e" stroke-width="1.3"/><path d="M1 1.2 L7 5.5 L13 1.2" fill="none" stroke="#3c3c3e" stroke-width="1.3"/></svg>
        </span>
        <span>marlene@quarrow.co<br>www.quarrow.co</span>
      </div>
      <div class="contact">
        <span class="contact__icon">
          <svg width="10" height="14" viewBox="0 0 10 14"><path d="M5 13.5 C5 13.5 0.8 8 0.8 5 A4.2 4.2 0 0 1 9.2 5 C9.2 8 5 13.5 5 13.5 Z" fill="#3c3c3e"/><circle cx="5" cy="5" r="1.6" fill="#fff"/></svg>
        </span>
        <span>14 Tellan Road<br>Singapore, 2281</span>
      </div>
    </div>
  </section>

  <section class="card card--back" aria-label="Business card back">
    <div class="back-name"><span class="line1">QUARROW</span><span class="line2">SIGNAL INSTRUMENTS</span></div>
  </section>
</body>
</html>
```